Marrowby Water Taxi and Transport Business Card

I need business cards for my new water taxi and freight transport business I have started here in Kodiak Alaska. Kodiak is a remote island in the middle of the gulf of Alaska. There are seven native villages around the island and Kodiak is the #2 fishing port in the United States. We also have the largest Coast Guard Base in the U.S. My company will be providing water taxi and freight transport logistics to the villages and many hunting and fishing lodges as well as remote properties around the island.

I would like a business card that isn't status quo, something that stands out, either in feel or appearance. I do like clean minimal designs but it needs to have the necessary contact info on it.

Target Market(s)

remote lodge / property owners, residents of the many villages around Kodiak and any one wanting to enjoy the great outdoors of Kodiak Alaska

Industry/Entity Type

Business

Contact Information for Business Card

I like clean simple designs that aren't cluttered but still provide the necessary information

Colors
0255a3
3277b5
33a4d5
9bcb3c
add136
fbed22
ffc214
f78f20
f37122

Requirements
Must have
• logo and contact info
• Captain Mason Elwick
• www.marrowbyferryline.com
• mason@marrowbyferryline.com

```html
<!DOCTYPE html>
<html lang="en">
<head>
<meta charset="utf-8">
<title>Marrowby Water Taxi and Transport – Business Card</title>
<link href="https://fonts.googleapis.com/css2?family=Montserrat:wght@600;700&family=Questrial&display=swap" rel="stylesheet">
<style>
  :root {
    --navy: #0255a3;
    --mid-blue: #3277b5;
    --sky: #33a4d5;
    --orange: #f78f20;
    --ink: #5a5a5a;
    --paper: #ffffff;
    --backdrop: #3a3a3a;
    --sea-deep: #0e3f86;
    --sea-light: #6fb6e6;
  }
  * { box-sizing: border-box; margin: 0; padding: 0; }
  html, body {
    width: 1105px; height: 1200px; overflow: hidden;
    background: var(--backdrop);
  }
  .sheet { position: relative; width: 1105px; height: 1200px; }
  .card {
    position: absolute; left: 196px; width: 720px; height: 411px;
    overflow: hidden;
  }
  .card--front { top: 146px; background: var(--paper); }
  .card--back { top: 602px; }

  .front-band { position: absolute; inset: 0; width: 720px; height: 411px; }

  .brand { position: absolute; left: 34px; top: 118px; }
  .brand__name {
    display: flex; align-items: center; gap: 12px;
    font-family: "Montserrat", sans-serif; font-weight: 700;
    font-size: 50px; line-height: 1; color: var(--navy);
  }
  .brand__dot { width: 22px; height: 22px; border-radius: 50%; background: var(--orange); }
  .brand__tagline {
    margin-top: 6px;
    font-family: "Montserrat", sans-serif; font-weight: 700;
    font-size: 19px; color: var(--navy);
  }

  .address {
    position: absolute; left: 34px; top: 232px;
    font-family: "Questrial", sans-serif; font-size: 19px; line-height: 25px;
    color: var(--ink); font-style: normal;
  }
  .contacts {
    position: absolute; left: 34px; top: 292px; list-style: none;
    font-family: "Questrial", sans-serif; font-size: 19px; color: var(--ink);
  }
  .contacts li { display: flex; align-items: center; gap: 12px; height: 28px; }
  .contacts svg { width: 18px; height: 18px; fill: var(--navy); flex: none; }

  .holder {
    position: absolute; right: 34px; top: 330px; text-align: right;
    color: var(--paper);
  }
  .holder__name {
    font-family: "Montserrat", sans-serif; font-weight: 700; font-size: 26px;
    letter-spacing: 0.5px;
  }
  .holder__role { font-family: "Questrial", sans-serif; font-size: 22px; margin-top: 4px; }

  .back-photo {
    position: absolute; inset: 0;
    background:
      linear-gradient(180deg, #2b6fd0 0%, #4a93e0 28%, #9fcdf0 40%, #1c3d6e 44%, var(--sea-deep) 60%, #1d5fae 80%, var(--sea-light) 100%);
  }
  .back-brand {
    position: absolute; left: 0; right: 0; top: 190px; text-align: center;
    color: var(--paper); font-family: "Montserrat", sans-serif; font-weight: 700;
  }
  .back-brand__name { font-size: 50px; line-height: 1; }
  .back-brand__tagline { font-size: 19px; margin-top: 6px; }
  .social { position: absolute; left: 0; right: 0; top: 349px; display: flex; justify-content: center; gap: 6px; }
  .social span { width: 29px; height: 29px; border-radius: 50%; background: var(--paper); }
</style>
</head>
<body>
<main class="sheet">

  <section class="card card--front" aria-label="Business card front">
    <svg class="front-band" viewBox="0 0 720 411" role="img" aria-label="Mountain range decoration in blue tones">
      <defs>
        <linearGradient id="bandFill" x1="0" y1="0" x2="0" y2="1">
          <stop offset="0" stop-color="#33a4d5"/>
          <stop offset="0.55" stop-color="#0255a3"/>
        </linearGradient>
      </defs>
      <polygon points="264,411 720,123 720,411" fill="url(#bandFill)"/>
    </svg>

    <div class="brand">
      <div class="brand__name"><span class="brand__dot"></span>Marrowby</div>
      <div class="brand__tagline">Water Taxi and Transport</div>
    </div>

    <address class="address">218 Tidewater Lane<br>Marrowby, Alaska 99615</address>

    <ul class="contacts">
      <li>
        <svg viewBox="0 0 24 24" aria-hidden="true"><path d="M6.6 10.8a15.1 15.1 0 0 0 6.6 6.6l2.2-2.2c.3-.3.7-.4 1-.2 1.1.4 2.3.6 3.6.6.6 0 1 .4 1 1V20c0 .6-.4 1-1 1A17 17 0 0 1 3 4c0-.6.4-1 1-1h3.5c.6 0 1 .4 1 1 0 1.3.2 2.5.6 3.6.1.3 0 .7-.2 1z"/></svg>
        555 014 2290
      </li>
      <li>
        <svg viewBox="0 0 24 24" aria-hidden="true"><path d="M2 5h20v14H2z M3.5 6.5 12 12.5l8.5-6" fill="none" stroke="#0255a3" stroke-width="2"/></svg>
        mason@marrowbyferryline.com
      </li>
      <li>
        <svg viewBox="0 0 24 24" aria-hidden="true"><circle cx="12" cy="12" r="10"/><path d="M2 12h20M12 2c3 3 3 17 0 20M12 2c-3 3-3 17 0 20" stroke="#fff" stroke-width="1.5" fill="none"/></svg>
        www.marrowbyferryline.com
      </li>
    </ul>

    <div class="holder">
      <div class="holder__name">MASON ELWICK</div>
      <div class="holder__role">Captain</div>
    </div>
  </section>

  <section class="card card--back" aria-label="Business card back">
    <div class="back-photo" role="img" aria-label="Photograph of a boat wake on a blue bay with distant hills under a clear sky"></div>
    <div class="back-brand">
      <div class="back-brand__name">Marrowby</div>
      <div class="back-brand__tagline">Water Taxi and Transport</div>
    </div>
    <div class="social" aria-hidden="true"><span></span><span></span><span></span></div>
  </section>

</main>
</body>
</html>
```